Fresh Start Bodywork Challenge 2017 Poster

We are having a Fresh Start Bodywork Challenge for 2017 at our fitness studio. We need a poster design using the template attached as a reference (Only reference). I have also included our Vorendal logo to put on the poster. Please DO NOT use the graphics in the flyer as we are expecting something much much better :-)
MUST HAVES:
- Size needed 11x17 with bleeding for printing
- .PSD File Format WITH LAYERS (CS3 Compatible)*** A MUST
- Use Vorendal Bootcamps Logo
- Use Information in the attached word doc

```html
<!DOCTYPE html>
<html lang="en">
<head>
<meta charset="utf-8">
<title>Fresh Start Bodywork Challenge 2017 Poster</title>
<link rel="stylesheet" href="https://fonts.googleapis.com/css2?family=Roboto+Condensed:wght@300;400;700&display=swap">
<style>
  :root {
    --stage: #d6d6d8;
    --ink: #000000;
    --ember-top: #5a1710;
    --ember-bottom: #2a0d08;
    --copper: #b8702a;
    --sky: #2a78c2;
    --slate: #231f20;
    --white: #ffffff;
  }
  * { margin: 0; padding: 0; box-sizing: border-box; }
  html, body { width: 933px; height: 1200px; overflow: hidden; background: var(--stage); }
  body { font-family: "Roboto Condensed", "Arial Narrow", sans-serif; color: var(--white); }
  .poster { position: absolute; left: 38px; top: 0; width: 857px; height: 1200px; background: var(--ink); overflow: hidden; }
  .header-band { position: absolute; left: 0; top: 0; width: 857px; height: 358px; background: linear-gradient(160deg, var(--ember-top) 0%, #471109 50%, var(--ember-bottom) 100%); }
  .brand { position: absolute; left: 81px; top: 50px; width: 388px; text-align: center; }
  .brand-name { font-size: 42px; font-weight: 700; letter-spacing: 1px; line-height: 1; }
  .brand-tagline { margin-top: 10px; font-size: 13px; font-weight: 700; letter-spacing: 2px; }
  .headline { position: absolute; left: 60px; width: 440px; text-align: center; line-height: 1; }
  .headline-intro { top: 176px; font-size: 38px; font-weight: 400; }
  .headline-main { top: 212px; font-size: 60px; font-weight: 700; color: var(--copper); }
  .headline-sub { top: 280px; font-size: 50px; font-weight: 300; letter-spacing: 24px; padding-left: 24px; }
  .athlete-photo { position: absolute; left: 381px; top: 145px; width: 476px; height: 728px; background: radial-gradient(ellipse at 55% 45%, #8a6a55 0%, #4a3328 38%, #1a1210 70%, rgba(0,0,0,0) 100%); }
  .pitch { position: absolute; left: 38px; top: 420px; line-height: 1.25; }
  .pitch-lead { font-size: 47px; font-weight: 700; }
  .pitch-line { font-size: 40px; font-weight: 400; }
  .pitch-accent { font-size: 54px; font-weight: 700; color: var(--copper); line-height: 1.15; }
  .duration-band { position: absolute; left: 0; top: 684px; width: 232px; height: 128px; background: var(--copper); }
  .duration-text { position: absolute; left: 38px; top: 700px; line-height: 0.95; }
  .duration-small { font-size: 46px; font-weight: 400; }
  .duration-big { font-size: 54px; font-weight: 700; }
  .duration-number { position: absolute; left: 206px; top: 650px; font-size: 200px; font-weight: 700; line-height: 1; }
  .schedule { position: absolute; left: 0; top: 873px; width: 857px; height: 64px; background: var(--slate); display: flex; align-items: center; }
  .schedule-item { text-align: center; line-height: 1.3; }
  .schedule-item + .schedule-item { border-left: 1px solid #8a8a8a; }
  .schedule-label { font-size: 18px; font-weight: 700; }
  .schedule-value { font-size: 18px; font-weight: 400; }
  .offer { position: absolute; top: 937px; height: 156px; display: flex; flex-direction: column; justify-content: center; align-items: center; text-align: center; line-height: 1.1; }
  .offer-price { left: 0; width: 428px; background: var(--sky); }
  .offer-price .small { font-size: 25px; font-weight: 400; }
  .offer-price .mid { font-size: 34px; font-weight: 400; }
  .offer-price .strong { font-size: 36px; font-weight: 700; }
  .offer-prize { left: 428px; width: 429px; background: var(--copper); }
  .offer-prize .amount { font-size: 64px; font-weight: 700; }
  .offer-prize .note { font-size: 46px; font-weight: 400; margin-top: 6px; }
  .contact { position: absolute; left: 0; top: 1100px; width: 857px; text-align: center; line-height: 1.2; }
  .contact-label { font-size: 34px; font-weight: 400; }
  .contact-url { font-size: 28px; font-weight: 400; }
</style>
</head>
<body>
  <main class="poster">
    <div class="header-band"></div>
    <div class="athlete-photo" role="img" aria-label="Photo of a fit athlete in black sportswear giving a thumbs up"></div>

    <div class="brand">
      <div class="brand-name">VORENDAL BOOTCAMPS</div>
      <div class="brand-tagline">THE ULTIMATE FITNESS SOLUTION</div>
    </div>

    <div class="headline headline-intro">FRESH START</div>
    <div class="headline headline-main">BODYWORK</div>
    <div class="headline headline-sub">CHALLENGE</div>

    <div class="pitch">
      <div class="pitch-lead">TRANSFORM</div>
      <div class="pitch-line">Your Body And Get In</div>
      <div class="pitch-line">The Best Shape Of</div>
      <div class="pitch-accent">Your Life!</div>
    </div>

    <div class="duration-band"></div>
    <div class="duration-text">
      <div class="duration-small">IN JUST</div>
      <div class="duration-big">WEEKS</div>
    </div>
    <div class="duration-number">6</div>

    <section class="schedule">
      <div class="schedule-item" style="width:282px">
        <div class="schedule-label">KICK OFF MEETING</div>
        <div class="schedule-value">Thursday, Jan 12th at 7:30 pm</div>
      </div>
      <div class="schedule-item" style="width:200px">
        <div class="schedule-label">START DATE</div>
        <div class="schedule-value">Tuesday, January 17th</div>
      </div>
      <div class="schedule-item" style="width:209px">
        <div class="schedule-label">END DATE</div>
        <div class="schedule-value">Saturday, February 25th</div>
      </div>
      <div class="schedule-item" style="width:166px">
        <div class="schedule-label">FINALE PARTY</div>
        <div class="schedule-value">March 2nd</div>
      </div>
    </section>

    <section class="offer offer-price">
      <div class="small">6 Weeks of Training, Nutrition, and</div>
      <div class="mid">COACHING STARTING</div>
      <div class="strong">AT JUST $99!</div>
    </section>
    <section class="offer offer-prize">
      <div class="amount">$500 CASH</div>
      <div class="note">Prize for Winner!</div>
    </section>

    <footer class="contact">
      <div class="contact-label">FOR MORE INFO</div>
      <div class="contact-url">www.vorendalbootcamps.com</div>
    </footer>
  </main>
</body>
</html>
```